Dallas Texas Special Event Center Flyer

Need a new brochure (small 8.5 x 11 tri-fold) for an event center in Dallas, Texas area. It is located on a golf course and is ideal for weddings, quinceaneras, retirement parties, etc. Is best known for weddings. There is no logo for the event center. I have attached the prior brochure, which is not professional. We do not have any site photos.

Target Market(s)

people seeking special event space in dallas, texas area. Brides, meeting planners, etc.

Industry/Entity Type

Golf Course

Font styles to use
Script
Other font styles liked:
• combine serif and some use of script ok

Requirements
Must have
• lots of photos - see attached

```html
<!DOCTYPE html>
<html lang="en">
<head>
<meta charset="utf-8">
<title>Event Center at Willowbend – Tri-fold Brochure</title>
<link rel="stylesheet" href="https://fonts.googleapis.com/css2?family=PT+Sans+Narrow:wght@400;700&family=Pinyon+Script&display=swap">
<style>
  :root {
    --ink: #0b0b0b;
    --white: #ffffff;
    --red: #d8253f;
    --backdrop: #e6e6e6;
    --script-ink: #1c1a16;
    --body-text: #f2f2f2;
  }
  * { box-sizing: border-box; margin: 0; padding: 0; }
  html, body { width: 1200px; height: 532px; overflow: hidden; }
  body {
    background: var(--backdrop);
    font-family: "PT Sans Narrow", "Arial Narrow", sans-serif;
    color: var(--white);
    position: relative;
  }
  .sheet {
    position: absolute;
    top: 31px;
    width: 577px;
    height: 444px;
    overflow: hidden;
    background: var(--ink);
    box-shadow: 0 2px 8px rgba(0,0,0,.25);
  }
  .sheet--outside { left: 19px; }
  .sheet--inside { left: 608px; }

  .header {
    position: absolute;
    top: 0;
    height: 98px;
    background: var(--ink);
    display: flex;
    align-items: center;
    justify-content: center;
    text-align: center;
  }
  .venue-name {
    font-size: 25px;
    line-height: 1;
    font-weight: 400;
    color: var(--white);
    text-align: center;
  }
  .contact-prompt { font-size: 15px; line-height: 1.15; }

  .photo { position: absolute; }
  .photo--bride-blur {
    left: 0; top: 98px; width: 192px; height: 346px;
    background: radial-gradient(ellipse at 55% 35%, #d8c8b4 0%, #a89580 45%, #6e5e50 100%);
  }
  .photo--centerpiece {
    left: 192px; top: 98px; width: 385px; height: 346px;
    background:
      radial-gradient(ellipse at 65% 60%, #6f7d3c 0%, rgba(111,125,60,0) 45%),
      linear-gradient(180deg, #e7b96c 0%, #c98a3f 45%, #7a4a22 80%, #4a2c16 100%);
  }
  .overlay-shade {
    position: absolute; left: 0; top: 98px; width: 192px; height: 346px;
    background: linear-gradient(180deg, rgba(0,0,0,0) 40%, rgba(40,30,25,.35) 100%);
  }
  .ornament {
    position: absolute;
    width: 32px; height: 10px;
    border-top: 1px solid rgba(255,255,255,.85);
    border-bottom: 1px solid rgba(255,255,255,.85);
  }
  .about {
    position: absolute;
    left: 14px; top: 283px; width: 164px;
    font-size: 10.3px; line-height: 15.2px;
    text-align: center;
    text-shadow: 0 1px 2px rgba(0,0,0,.35);
  }

  .banner-web {
    position: absolute; left: 192px; top: 98px; width: 193px; height: 32px;
    background: var(--red);
    font-size: 10.5px;
    display: flex; align-items: center; justify-content: center;
  }
  .ribbon-size {
    position: absolute; left: 385px; top: 98px; width: 192px; height: 32px;
  }
  .ribbon-size svg { position: absolute; inset: 0; }
  .ribbon-size span {
    position: relative;
    display: block;
    padding: 6px 0 0 56px;
    font-size: 17px; font-weight: 700; font-style: italic;
  }
  .tagline {
    position: absolute; left: 392px; top: 142px; width: 182px;
    font-family: "Pinyon Script", cursive;
    font-size: 19px; line-height: 21px;
    color: var(--script-ink);
    text-align: center;
  }
  .contact {
    position: absolute; left: 192px; top: 138px; width: 193px;
    text-align: center;
  }
  .contact-name { font-size: 15.5px; line-height: 20px; }
  .contact-email { font-size: 9.5px; line-height: 14px; }
  .contact-phone { font-size: 14px; line-height: 18px; }

  .ribbon-address {
    position: absolute; left: 202px; top: 227px; width: 174px; height: 66px;
  }
  .ribbon-address svg { position: absolute; inset: 0; }
  .ribbon-address p {
    position: relative;
    text-align: center;
    padding-top: 5px;
  }
  .address-label { font-size: 11px; line-height: 16px; }
  .address-line { font-size: 15px; line-height: 20px; }

  .info-panel {
    position: absolute; left: 0; top: 0; width: 192px; height: 444px;
    background: var(--ink);
  }
  .info-panel .header { width: 192px; height: 70px; }
  .info-panel .ornament { left: 80px; top: 86px; }
  .info-body {
    position: absolute; left: 14px; top: 106px; width: 164px;
    font-size: 7.6px; line-height: 10.4px;
    text-align: center;
    color: var(--body-text);
  }
  .info-body p + p { margin-top: 10.4px; }

  .tile { position: absolute; }
  .tile--toast { left: 192px; top: 0; width: 205px; height: 169px; background: linear-gradient(150deg, #c7b296 0%, #8a7058 55%, #3d3128 100%); }
  .tile--microphone { left: 192px; top: 171px; width: 110px; height: 75px; background: linear-gradient(135deg, #d8c29a, #8c7452); }
  .tile--table-flowers { left: 304px; top: 171px; width: 93px; height: 75px; background: linear-gradient(135deg, #f1efec, #bdb7c6); }
  .tile--cake { left: 192px; top: 248px; width: 205px; height: 116px; background: linear-gradient(160deg, #d6a58a 0%, #f4e7c8 50%, #e7cfa6 100%); }
  .tile--bride-portrait { left: 192px; top: 366px; width: 58px; height: 78px; background: linear-gradient(180deg, #b9a79a, #ece4de); }
  .tile--dress-bow { left: 252px; top: 366px; width: 145px; height: 78px; background: linear-gradient(135deg, #f3dcd4, #d9a79a); }
  .tile--bouquets { left: 399px; top: 0; width: 178px; height: 121px; background: linear-gradient(180deg, #f5efe9, #e8c9cc); }
  .tile--couple { left: 399px; top: 123px; width: 178px; height: 123px; background: linear-gradient(160deg, #9aa86a 0%, #d9c9b8 60%, #e8d7ce 100%); }
  .tile--bridesmaids { left: 399px; top: 248px; width: 178px; height: 82px; background: linear-gradient(135deg, #e9c3bd, #f7f1ec); }
  .tile--cake-cutting { left: 399px; top: 332px; width: 178px; height: 112px; background: linear-gradient(150deg, #4a3a30 0%, #d9cbc0 55%, #f4eeea 100%); }
</style>
</head>
<body>

<section class="sheet sheet--outside" aria-label="Brochure outside">
  <div class="photo photo--bride-blur" role="img" aria-label="Soft-focus photo of a bride at a reception"></div>
  <div class="overlay-shade"></div>
  <div class="photo photo--centerpiece" role="img" aria-label="Photo of a rose and berry centerpiece on a set banquet table"></div>

  <header class="header" style="left:0;width:192px;">
    <h1 class="venue-name">Event Center<br>at Willowbend</h1>
  </header>
  <div class="header" style="left:192px;width:193px;">
    <p class="contact-prompt">Contact us for more<br>information or visit<br>us at:</p>
  </div>
  <div class="header" style="left:385px;width:192px;">
    <p class="venue-name">Event Center<br>at Willowbend</p>
  </div>

  <div class="ornament" role="img" aria-label="Small decorative flourish" style="left:80px;top:264px;"></div>
  <p class="about">The Event Center at Willowbend is located on Willowbend Golf Course, an 18-hole, 215-acre championship golf course in Harlow, Texas and is surrounded by rolling hills, seven beautiful lakes, creeks, pecan orchards and many varieties of wildlife.</p>

  <div class="banner-web">www.eventcenteratwillowbend.com</div>
  <div class="ribbon-size">
    <svg width="192" height="32" viewBox="0 0 192 32"><polygon points="0,0 192,0 178,16 192,32 0,32" fill="var(--red)"/></svg>
    <span>12,000 ft²</span>
  </div>

  <p class="tagline">Host your event at the Dallas area's premiere event venue</p>

  <div class="contact">
    <p class="contact-name">Marla Penrose</p>
    <p class="contact-email">marla@eventcenteratwillowbend.com</p>
    <p class="contact-phone">214-555-0147</p>
    <p class="contact-phone">972-555-0193</p>
  </div>

  <div class="ribbon-address">
    <svg width="174" height="66" viewBox="0 0 174 66"><polygon points="0,0 174,0 162,66 0,66 12,33" fill="var(--red)"/></svg>
    <p>
      <span class="address-label">Event Center at Willowbend</span><br>
      <span class="address-line">4810 W Ridge Road</span><br>
      <span class="address-line">Harlow, TX 75199</span>
    </p>
  </div>
</section>

<section class="sheet sheet--inside" aria-label="Brochure inside">
  <div class="info-panel">
    <header class="header">
      <h2 class="venue-name">Event Center<br>at Willowbend</h2>
    </header>
    <div class="ornament" role="img" aria-label="Small decorative flourish"></div>
    <div class="info-body">
      <p>The Event Center at Willowbend offers a 12,000 square foot facility which boasts a Grand Ballroom and two Banquet rooms.</p>
      <p>The grand ballroom will accommodate 809 guests for a wedding ceremony and reception, quinceanera, retirement party or any occasion that demands a large-scale, elegant setting.</p>
      <p>The bridal suite at the top of the winding staircase allows the Bride and her bridesmaids to prepare for the big day out of sight of arriving guests, allowing a dramatic grand entrance.</p>
      <p>Banquet room 1 will accommodate 103 guests for a mid-size, private event such as a birthday or retirement party or company holiday party while Banquet room 2 will accommodate 35 guests for a small intimate event such as a bridal shower, bridesmaid's luncheon or corporate training. The rooms can be used separately or together.</p>
      <p>The event center has a full commercial kitchen onsite to cater any event from formal dining to buffet-style. The menu can be customized to your specifications and will be prepared by our expert chef and his team.</p>
      <p>The Event Center at Willowbend is the perfect location for your wedding, conference, seminar, party, reunion or graduation.</p>
    </div>
  </div>

  <div class="tile tile--toast" role="img" aria-label="Photo of wedding guests raising champagne glasses in a toast"></div>
  <div class="tile tile--microphone" role="img" aria-label="Photo of a microphone in a conference hall"></div>
  <div class="tile tile--table-flowers" role="img" aria-label="Photo of white floral arrangements on banquet tables"></div>
  <div class="tile tile--cake" role="img" aria-label="Close-up photo of a wedding cake with sugar roses"></div>
  <div class="tile tile--bride-portrait" role="img" aria-label="Photo of a bride in a veil"></div>
  <div class="tile tile--dress-bow" role="img" aria-label="Photo of the back of a wedding dress with a bow"></div>
  <div class="tile tile--bouquets" role="img" aria-label="Photo of pink and white rose bouquets in glass vases"></div>
  <div class="tile tile--couple" role="img" aria-label="Photo of a wedding couple walking through guests outdoors"></div>
  <div class="tile tile--bridesmaids" role="img" aria-label="Photo of bridesmaids holding white bouquets"></div>
  <div class="tile tile--cake-cutting" role="img" aria-label="Photo of a couple cutting a tiered wedding cake"></div>
</section>

</body>
</html>
```